Corvane Freight Company Business Card Design

We are a company that delivers natural saltwater (from the ocean) to aquarium companies, restaurants and home marine tanks. I would like a new business card to suit.

Must include Name, company name, abn, contact number and website as well as logo (see attached).

Looking for a design that stands out, has a clean but unique appearance.

Double and single sided entries welcome

Business

• Logo

```html
<!DOCTYPE html>
<html lang="en">
<head>
<meta charset="utf-8">
<title>Corvane Freight Company – Business Cards</title>
<link href="https://fonts.googleapis.com/css2?family=Source+Sans+3:wght@400;600;700&display=swap" rel="stylesheet">
<style>
  :root {
    --stage: #1c1c1c;
    --card: #ffffff;
    --ocean-deep: #0f5fae;
    --ocean-light: #56c8f2;
    --brand: #1e9ad6;
    --name: #1a8cd0;
    --ink-grey: #6a6a6a;
    --info: #2f6fb5;
    --rule: #b9b9b9;
  }
  * { margin: 0; padding: 0; box-sizing: border-box; }
  html, body { width: 1200px; height: 750px; overflow: hidden; background: var(--stage); }
  body { position: relative; font-family: "Source Sans 3", sans-serif; }

  .card {
    position: absolute;
    width: 516px;
    height: 294px;
    background: var(--card);
    overflow: hidden;
  }
  .card--front-deep  { left: 73px;  top: 64px; }
  .card--front-light { left: 607px; top: 65px; }
  .card--back        { left: 342px; top: 400px; background: var(--ocean-light); }

  .tab {
    position: absolute;
    left: 90px;
    width: 340px;
    height: 12px;
  }
  .tab--top    { top: -2px;    border-radius: 0 0 12px 12px; }
  .tab--bottom { bottom: -2px; border-radius: 12px 12px 0 0; }
  .card--front-deep  .tab { background: var(--ocean-deep); }
  .card--front-light .tab { background: var(--ocean-light); }

  .brand-name {
    position: absolute;
    left: 18px;
    top: 134px;
    width: 240px;
    text-align: center;
    font-weight: 600;
    font-size: 22px;
    line-height: 1;
    color: var(--brand);
    white-space: nowrap;
  }

  .divider {
    position: absolute;
    left: 268px;
    top: 60px;
    width: 1px;
    height: 176px;
    background: linear-gradient(to bottom, transparent, var(--rule) 15%, var(--rule) 85%, transparent);
  }

  .contact {
    position: absolute;
    left: 287px;
    top: 64px;
    color: var(--info);
    font-size: 13px;
    line-height: 18px;
  }
  .contact__name { font-weight: 700; font-size: 19px; line-height: 22px; color: var(--name); }
  .contact__title { font-size: 15px; line-height: 20px; color: var(--ink-grey); margin-bottom: 10px; }
  .contact__line { display: flex; align-items: center; gap: 6px; }
  .contact__line svg { width: 10px; height: 10px; fill: none; stroke: var(--info); stroke-width: 1.4; }
  .contact__address { margin-top: 20px; }

  .back-name {
    position: absolute;
    inset: 0;
    display: flex;
    align-items: center;
    justify-content: center;
    font-weight: 600;
    font-size: 42px;
    color: #ffffff;
    white-space: nowrap;
  }
</style>
</head>
<body>

  <section class="card card--front-deep">
    <div class="tab tab--top"></div>
    <div class="brand-name">Corvane Freight Company</div>
    <div class="divider"></div>
    <div class="contact">
      <p class="contact__name">Your Name</p>
      <p class="contact__title">Title</p>
      <p class="contact__line"><svg viewBox="0 0 10 10"><path d="M2 1.5l1.8 0 .7 2-1 .8a5 5 0 0 0 2.2 2.2l.8-1 2 .7v1.8A1 1 0 0 1 7.5 9 6.5 6.5 0 0 1 1 2.5a1 1 0 0 1 1-1z"/></svg>123-456-7892</p>
      <p class="contact__line"><svg viewBox="0 0 10 10"><circle cx="5" cy="5" r="4"/><ellipse cx="5" cy="5" rx="1.8" ry="4"/><path d="M1 5h8"/></svg>www.corvanefreight.com</p>
      <div class="contact__address">
        <p>Street Name, City Name ,</p>
        <p>State, Zip Code</p>
        <p>ABN: 123456789</p>
      </div>
    </div>
    <div class="tab tab--bottom"></div>
  </section>

  <section class="card card--front-light">
    <div class="tab tab--top"></div>
    <div class="brand-name">Corvane Freight Company</div>
    <div class="divider"></div>
    <div class="contact">
      <p class="contact__name">Your Name</p>
      <p class="contact__title">Title</p>
      <p class="contact__line"><svg viewBox="0 0 10 10"><path d="M2 1.5l1.8 0 .7 2-1 .8a5 5 0 0 0 2.2 2.2l.8-1 2 .7v1.8A1 1 0 0 1 7.5 9 6.5 6.5 0 0 1 1 2.5a1 1 0 0 1 1-1z"/></svg>123-456-7892</p>
      <p class="contact__line"><svg viewBox="0 0 10 10"><circle cx="5" cy="5" r="4"/><ellipse cx="5" cy="5" rx="1.8" ry="4"/><path d="M1 5h8"/></svg>www.corvanefreight.com</p>
      <div class="contact__address">
        <p>Street Name, City Name ,</p>
        <p>State, Zip Code</p>
        <p>ABN: 123456789</p>
      </div>
    </div>
    <div class="tab tab--bottom"></div>
  </section>

  <section class="card card--back">
    <div class="back-name">Corvane Freight Company</div>
  </section>

</body>
</html>
```